Design logo, business cards, and web page for new web and bi development consulting company

I've started a Web and Business Intelligence development consulting company. We develop on Quordex's stack, Visual Sudio and Tessel Server. We develop responsive web sites and business intelligence platforms. I plan on focusing on small to medium sized business as my client base. I need a logo, business cards, and a one page web site. We will do more with the web site with you in the next six months if the business survives. The name of the company is Corvalo Integration Solutions, Corvalo for short.

Target Market(s)

small to medium sized businesses

Industry/Entity Type

Business

Contact Information for Business Card

logo
name
title
email
phone

Logo Text

Corvalo Integration Solutions - web and data solutions

Coding

Coded - Design and coding required

Number of Pages Required

1 page

Font styles to use
Sans Serif

Colors
0355a3
0092cd
00a88f
6b449b

Requirements
Nice to have
• web and data solutions

```html
<!DOCTYPE html>
<html lang="en">
<head>
<meta charset="utf-8">
<title>Corvalo Integration Solutions</title>
<link rel="stylesheet" href="https://fonts.googleapis.com/css2?family=Roboto+Condensed:wght@300;400;700&family=Roboto:wght@300;400;500&display=swap">
<style>
:root{
  --blue:#1588d4;
  --blue-dark:#0b4d9e;
  --teal:#0a9c8a;
  --red:#c4161c;
  --ink:#333;
  --muted:#777;
  --line:#e6e6e6;
  --footer:#121212;
}
*{margin:0;padding:0;box-sizing:border-box}
html,body{width:858px;height:1200px;overflow:hidden;background:#fff}
body{position:relative;font-family:'Roboto',sans-serif;color:var(--ink)}
.abs{position:absolute}
.cond{font-family:'Roboto Condensed',sans-serif}
.brand{left:42px;top:26px;font-family:'Roboto Condensed',sans-serif;font-weight:300;font-size:24px;letter-spacing:2px;color:#333}
.top-links{right:42px;top:32px;display:flex;gap:18px;font-family:'Roboto Condensed',sans-serif;font-size:9.5px;color:#555}
.top-links span{display:flex;align-items:center;gap:5px}
.nav{left:0;top:78px;width:858px;height:32px;background:var(--blue)}
.nav a{position:absolute;top:0;height:32px;line-height:32px;color:#fff;font-family:'Roboto Condensed',sans-serif;font-size:10px;text-decoration:none}
.nav .active{left:42px;width:68px;text-align:center;background:var(--blue-dark)}
.nav .sep{position:absolute;top:10px;width:1px;height:14px;background:rgba(255,255,255,.35)}
.hero{left:0;top:110px;width:858px;height:358px;background:linear-gradient(90deg,#8e9095 0%,#b9bbbf 30%,#6a6d74 55%,#4b4f57 75%,#9a9ca1 100%)}
.hero-title{left:42px;top:146px;font-family:'Roboto Condensed',sans-serif;font-size:22px;line-height:34px;color:#fff;text-transform:uppercase;text-shadow:0 1px 3px rgba(0,0,0,.6)}
.dots{left:416px;top:329px;display:flex;gap:3px}
.dots i{width:7px;height:7px;border-radius:50%;border:1px solid #fff;display:block}
.dots i.on{background:#fff}
.hero-shadow{left:20px;top:468px;width:818px;height:12px;background:radial-gradient(ellipse at top,rgba(0,0,0,.22),rgba(0,0,0,0) 70%)}
h2{position:absolute;font-family:'Roboto Condensed',sans-serif;font-weight:400;font-size:18px;color:#333}
.lead{font-family:'Roboto Condensed',sans-serif;font-size:11px;line-height:17px;color:#333}
.body{font-weight:300;font-size:9px;line-height:17px;color:#666}
.photo{border:3px solid #fff;box-shadow:0 1px 4px rgba(0,0,0,.3)}
.btn{left:274px;top:687px;width:92px;height:26px;background:var(--blue);color:#fff;font-family:'Roboto Condensed',sans-serif;font-size:10px;line-height:26px;text-align:center;border-radius:3px;box-shadow:1px 2px 2px rgba(0,0,0,.25)}
.vline{left:538px;top:505px;width:1px;height:222px;background:var(--line)}
.hline{left:0;width:858px;height:1px;background:#eee}
.ticks{left:586px;top:616px;list-style:none;font-size:9px;color:var(--teal)}
.ticks li{height:19.5px;display:flex;align-items:center;gap:8px}
.ticks li span{text-decoration:underline}
.step-num{width:34px;height:34px;border-radius:50%;border:2px solid var(--blue);box-shadow:0 0 0 2px #dbe8f3;color:var(--blue);font-family:'Roboto Condensed',sans-serif;font-size:17px;line-height:30px;text-align:center}
.teal-title{font-family:'Roboto Condensed',sans-serif;font-size:12px;color:var(--teal)}
.link-red{font-size:9px;color:var(--red);text-decoration:underline;font-family:'Roboto Condensed',sans-serif}
.box-art{width:60px;height:68px;background:linear-gradient(160deg,#e8ecf3,#2f67c7 70%,#1d3f8a)}
.date{left:565px;top:963px;width:48px;height:53px;background:var(--blue);border-top:4px solid var(--blue-dark);color:#fff;text-align:center;font-family:'Roboto Condensed',sans-serif}
.footer{left:0;top:1113px;width:858px;height:87px;background:var(--footer)}
.f-text{font-family:'Roboto Condensed',sans-serif;font-size:9.5px;color:#8a8a8a}
.social{width:24px;height:24px;border-radius:50%;background:#2c2c2c}
</style>
</head>
<body>
<div class="abs brand">CORVALO</div>
<div class="abs top-links">
  <span><svg width="9" height="9" viewBox="0 0 10 10"><circle cx="5" cy="3" r="2.5" fill="var(--blue)"/><path d="M0 10a5 4 0 0 1 10 0z" fill="var(--blue)"/></svg>My Account</span>
  <span><svg width="9" height="9" viewBox="0 0 10 10"><rect x="1" y="4.5" width="8" height="5.5" fill="var(--blue)"/><path d="M3 4.5V3a2 2 0 0 1 4 0v1.5" stroke="var(--blue)" fill="none" stroke-width="1.4"/></svg>Login</span>
  <span><svg width="9" height="9" viewBox="0 0 10 10"><circle cx="5" cy="5" r="3.6" fill="none" stroke="var(--blue)" stroke-width="2.2" stroke-dasharray="2 1.2"/><circle cx="5" cy="5" r="1.2" fill="var(--blue)"/></svg>Support</span>
</div>

<nav class="abs nav">
  <a class="active">HOME</a>
  <a style="left:132px">ABOUT US</a><i class="sep" style="left:197px"></i>
  <a style="left:218px">SERVICES</a><i class="sep" style="left:281px"></i>
  <a style="left:302px">CLIENT</a><i class="sep" style="left:353px"></i>
  <a style="left:375px">NEWS</a><i class="sep" style="left:422px"></i>
  <a style="left:443px">CONTACT US</a>
</nav>

<div class="abs hero" role="img" aria-label="Photo of a smiling business team standing together in an office"></div>
<div class="abs hero-title">Nemo enim ipsam voluptas<br>aspernatur</div>
<div class="abs dots"><i class="on"></i><i></i><i></i></div>
<div class="abs hero-shadow"></div>

<h2 style="left:42px;top:505px">Welcome to our Company</h2>
<div class="abs photo" role="img" aria-label="Photo of colleagues working at computers in a bright office" style="left:42px;top:552px;width:210px;height:163px;background:linear-gradient(135deg,#c9b7a4,#e9ecef 45%,#b7c2cf)"></div>
<div class="abs lead" style="left:274px;top:553px;width:250px">Neque porro quisquam est, qui dolorem ipsum quia dolor sit , sed quia non numquam</div>
<div class="abs body" style="left:274px;top:595px;width:250px">sed quia non numquam eius modi tempora incidunt ut labore et dolore magnam aliquam quaerat voluptatem. Ut enim ad minima veniam, quis nostrum exercitationem ullam corporis suscipit laboriosam, nisi ut</div>
<div class="abs btn">More Info</div>
<div class="abs vline"></div>

<h2 style="left:562px;top:505px">Technical Solution</h2>
<div class="abs lead" style="left:564px;top:553px">Neque porro quisquam est, qui dolorem ipsum quia</div>
<div class="abs body" style="left:564px;top:575px;width:250px">sed quia non numquam eius modi tempora incidunt ut labore et dolore magnam aliquam quaerat voluptatem.</div>
<ul class="abs ticks">
  <li><svg width="9" height="8" viewBox="0 0 9 8"><path d="M1 4l2.5 2.5L8 1" stroke="var(--teal)" stroke-width="2" fill="none"/></svg><span>sed quia &nbsp;numquam eius modi tempora</span></li>
  <li><svg width="9" height="8" viewBox="0 0 9 8"><path d="M1 4l2.5 2.5L8 1" stroke="var(--teal)" stroke-width="2" fill="none"/></svg><span>sed quia &nbsp;numquam eius modi tempora</span></li>
  <li><svg width="9" height="8" viewBox="0 0 9 8"><path d="M1 4l2.5 2.5L8 1" stroke="var(--teal)" stroke-width="2" fill="none"/></svg><span>sed quia &nbsp;numquam eius modi tempora</span></li>
  <li><svg width="9" height="8" viewBox="0 0 9 8"><path d="M1 4l2.5 2.5L8 1" stroke="var(--teal)" stroke-width="2" fill="none"/></svg><span>sed quia &nbsp;numquam eius modi tempora</span></li>
</ul>

<div class="abs hline" style="top:747px"></div>
<h2 style="left:42px;top:766px">What We Do</h2>

<div class="abs step-num" style="left:45px;top:820px">1</div>
<div class="abs teal-title" style="left:97px;top:818px">Quordex's Stack</div>
<div class="abs body" style="left:97px;top:834px;width:180px;line-height:14px">sed quia non numquam eius &nbsp;temporala-bore et dolore magnam aliquam</div>

<div class="abs step-num" style="left:317px;top:820px">2</div>
<div class="abs teal-title" style="left:369px;top:818px">Lumio Studio &amp; Tessel Server</div>
<div class="abs body" style="left:369px;top:834px;width:180px;line-height:14px">sed quia non numquam eius &nbsp;temporala-bore et dolore magnam aliquam</div>

<div class="abs step-num" style="left:588px;top:820px">3</div>
<div class="abs teal-title" style="left:640px;top:818px">Lumio Studio &amp; Tessel Server</div>
<div class="abs body" style="left:640px;top:834px;width:180px;line-height:14px">sed quia non numquam eius &nbsp;temporala-bore et dolore magnam aliquam</div>

<div class="abs hline" style="top:898px"></div>
<h2 style="left:42px;top:927px">Latest Projects</h2>

<div class="abs box-art" role="img" aria-label="Illustration of a software box with a disc" style="left:42px;top:973px"></div>
<div class="abs teal-title" style="left:113px;top:970px">Project Name</div>
<div class="abs body" style="left:113px;top:990px;width:162px;line-height:14px;text-align:justify">iste natus error sit voluptatem accusan-tium doloremque laudantium, totam rem aperiam, eaque ipsa quae ab illo</div>
<div class="abs link-red" style="left:113px;top:1041px">More Info</div>

<div class="abs box-art" role="img" aria-label="Illustration of a software box with a disc" style="left:297px;top:973px"></div>
<div class="abs teal-title" style="left:369px;top:970px">Project Name</div>
<div class="abs body" style="left:369px;top:990px;width:162px;line-height:14px;text-align:justify">iste natus error sit voluptatem accusan-tium doloremque laudantium, totam rem aperiam, eaque ipsa quae ab illo</div>
<div class="abs link-red" style="left:369px;top:1041px">More Info</div>

<h2 style="left:562px;top:926px">Our Updates</h2>
<div class="abs date"><div style="font-size:17px;margin-top:5px;line-height:19px">12</div><div style="font-size:12px">FEB</div></div>
<div class="abs lead" style="left:627px;top:961px;width:170px;line-height:14px;text-align:justify">Neque porro quisquam est lorem ipsum quia dolor sit amet &nbsp;quia non numquam eius</div>
<div class="abs cond" style="left:627px;top:1009px;font-size:8.5px;color:var(--red)">BY LENA MARSH</div>
<div class="abs body" style="left:565px;top:1025px;width:240px">non numquam eius modi tempora incidunt ut labore et dolore magnam aliquam quaerat voluptatem.</div>
<div class="abs link-red" style="left:565px;top:1060px">Read More</div>

<footer class="abs footer">
  <div class="abs f-text" style="left:42px;top:27px">About &nbsp;| &nbsp;Terms &nbsp;| &nbsp;Privacy Policy</div>
  <div class="abs f-text" style="left:42px;top:47px">All Rights Reserved. Copyrights © 2014.</div>
  <div class="abs f-text" style="left:278px;top:25px">Newsletter Signup</div>
  <div class="abs" style="left:279px;top:42px;width:118px;height:19px;background:#d6d6d6;font-size:8px;color:#777;line-height:19px;padding-left:9px">Email Address</div>
  <div class="abs" style="left:397px;top:42px;width:50px;height:19px;background:#555;font-size:8px;color:#eee;line-height:19px;text-align:center">Subscribe</div>
  <svg class="abs" style="left:513px;top:29px" width="30" height="30" viewBox="0 0 30 30"><circle cx="15" cy="15" r="14" fill="none" stroke="#777" stroke-width="1.5"/><path d="M10 8c-2 2 0 8 4 11s7 4 8 2l-2.5-2.5-2 1c-2-1-4-3-5-5l1-2L11 8z" fill="#777"/></svg>
  <div class="abs f-text" style="left:549px;top:27px;font-size:9px">Call Us:</div>
  <div class="abs cond" style="left:549px;top:37px;font-size:15px;color:#8a8a8a">045-7310-2246</div>
  <div class="abs social" style="left:709px;top:30px"></div>
  <div class="abs social" style="left:736px;top:30px"></div>
  <div class="abs social" style="left:763px;top:30px"></div>
  <div class="abs social" style="left:790px;top:30px"></div>
</footer>
</body>
</html>
```